skincare creams for tired moms

I need a package and a logo design for a skincare company based in California called Petal Ledger. I make day and night cream, under eye cream, and body lotion. The first product I plan to launch is an under eye cream. It does not have to be in these colors but I do teals, greens, black, and cobalt blue.

The package is going to either be in a box or a bag. Either way I go it will be like a gift box or bag. The design should make the person feel like they are getting something special and luxurious just for them.
Updates

I have small kids and it is really difficult to find a chunk of time to myself to update or review.

Need extra days to review

Target Market(s)

mainly first time moms. I am making an under eye cream that does not use retinol but is still powerful enough to get rid of bags and dark circles.

Industry/Entity Type

Cosmetics

Logo Text

The package and logo should incorporate the name Petal Ledger.

Font styles to use
Decorative
Script

Colors

Designer to choose colors to be used in the design.

Requirements
Nice to have
• maybe focus more on Ledger instead of Petal. Also incorporate plants or flowers
Should not have
• not a huge fan of pink

```html
<!DOCTYPE html>
<html lang="en">
<head>
<meta charset="utf-8">
<title>Petal Ledger — Under Eye Cream Package</title>
<link rel="stylesheet" href="https://fonts.googleapis.com/css2?family=Playfair+Display:wght@900&family=Cormorant+Garamond:wght@300&family=Fira+Sans+Condensed:wght@400&display=swap">
<style>
  :root {
    --paper: #ffffff;
    --teal: #019394;
    --cobalt: #1f50a2;
    --leaf: #63c07a;
    --mist: #6f93d3;
    --label-white: #ffffff;
  }
  html, body {
    margin: 0;
    padding: 0;
    width: 1200px;
    height: 1036px;
    overflow: hidden;
    background: var(--paper);
  }
  .canvas {
    position: relative;
    width: 1200px;
    height: 1036px;
    background: var(--paper);
  }
  .package {
    position: absolute;
    left: 450px;
    top: 0;
    width: 314px;
    height: 1036px;
  }
  .lid-band {
    position: absolute;
    left: 0;
    top: 0;
    width: 314px;
    height: 104px;
    background: var(--teal);
  }
  .brand {
    position: absolute;
    left: 0;
    top: 180px;
    width: 314px;
    text-align: center;
    color: var(--cobalt);
    font-family: "Playfair Display", Georgia, serif;
    font-weight: 900;
  }
  .brand-name {
    display: block;
    font-size: 58px;
    line-height: 60px;
    letter-spacing: 6px;
    padding-left: 6px;
  }
  .brand-sub {
    display: block;
    margin-top: 12px;
    font-size: 12px;
    letter-spacing: 12px;
    padding-left: 12px;
  }
  .front-panel {
    position: absolute;
    left: 0;
    top: 357px;
    width: 314px;
    height: 679px;
    background: var(--cobalt);
    overflow: hidden;
  }
  .bloom-art {
    position: absolute;
    left: 94px;
    top: 105px;
    width: 220px;
    height: 370px;
    background: radial-gradient(ellipse 100% 55% at 100% 57%, rgba(99,192,122,0.55) 0%, rgba(99,192,122,0.25) 45%, rgba(99,192,122,0) 100%);
  }
  .product-name {
    position: absolute;
    left: 28px;
    top: 581px;
    margin: 0;
    font-family: "Cormorant Garamond", Georgia, serif;
    font-weight: 300;
    font-size: 11px;
    letter-spacing: 10.4px;
    color: var(--mist);
    white-space: nowrap;
  }
  .product-size {
    position: absolute;
    left: 28px;
    top: 635px;
    margin: 0;
    font-family: "Fira Sans Condensed", Arial, sans-serif;
    font-size: 10px;
    color: var(--label-white);
  }
</style>
</head>
<body>
  <main class="canvas">
    <section class="package">
      <div class="lid-band"></div>
      <h1 class="brand">
        <span class="brand-name">PETAL</span>
        <span class="brand-sub">LEDGER</span>
      </h1>
      <div class="front-panel">
        <div class="bloom-art" role="img" aria-label="Line illustration of a green flower with long curling stamens radiating from the right edge"></div>
        <p class="product-name">UNDER&nbsp;&nbsp;EYE&nbsp;&nbsp;CREAM</p>
        <p class="product-size">0.5 OZ</p>
      </div>
    </section>
  </main>
</body>
</html>
```